Quendle Pools & Patio Homepage Design

I am looking for someone to design a one-page website for a company called Quendle Pools & Patio. While the content will be different, the design should be similar to https://quendle-example.com/pools-patio/.
Industry/Entity Type
Pool Cleaning Service
Number of Pages Required
1 page
Font styles to use
Other font styles liked:
- See brand guidelines

Requirements
Must have
- Must be similar in style https://quendle-example.com/pools-patio/. Look at the Word Doc for the content.

```html
<!DOCTYPE html>
<html lang="en">
<head>
<meta charset="utf-8">
<title>Quendle Pools &amp; Patio</title>
<link rel="stylesheet" href="https://fonts.googleapis.com/css2?family=Fredoka:wght@500&family=Roboto+Slab:wght@400;700&display=swap">
<style>
:root{
  --green:#6cc20a;
  --green-dark:#57a300;
  --blue:#1d8ad8;
  --blue-deep:#1672c0;
  --ink:#2f2f2f;
  --muted:#555;
  --line:#e3e3e3;
  --soft-blue:#eef5f9;
  --soft-green:#f4f7ee;
  --white:#fff;
}
*{box-sizing:border-box;margin:0;padding:0}
html,body{width:1200px;height:4145px;overflow:hidden}
body{position:relative;font-family:"Roboto Slab",Georgia,serif;color:var(--ink);background:var(--white)}
.abs{position:absolute}
.display{font-family:"Fredoka",sans-serif;font-weight:500}
.btn{position:absolute;display:flex;align-items:center;justify-content:center;background:var(--green);color:var(--white);font-weight:700;font-size:13px;text-transform:uppercase;letter-spacing:.3px}
.btn-blue{background:var(--blue)}
.section-title{position:absolute;left:0;width:1200px;text-align:center;color:var(--blue);font-size:40px}
.section-title::after{content:"";display:block;width:76px;height:3px;background:var(--green);margin:6px auto 0}
/* header */
.header{top:0;left:0;width:1200px;height:137px;background:var(--white)}
.brand{display:flex;align-items:center;gap:12px}
.brand-mark{width:46px;height:46px;background:var(--green);border-radius:8px}
.brand-name{font-size:52px;color:var(--blue);line-height:1}
.call{left:710px;top:28px;display:flex;gap:12px;align-items:center}
.call small{display:block;font-size:10px;font-weight:700;color:var(--ink)}
.call b{font-size:16px;color:var(--blue);letter-spacing:1px}
.social{display:flex;gap:10px}
.social span{width:36px;height:36px;border-radius:50%;background:var(--white);border:1px solid var(--line);box-shadow:0 2px 6px rgba(0,0,0,.12)}
.social span:first-child{background:var(--green);border-color:var(--green)}
.nav{top:91px;left:509px;display:flex;gap:40px;font-size:15px;font-weight:700}
.nav .on{color:var(--green)}
/* hero */
.hero{top:137px;left:0;width:1200px;height:600px;background:linear-gradient(160deg,#3d6a3a 0%,#6e8a55 22%,#4a9fc6 48%,#2a9bd6 70%,#57bfe6 100%)}
.hero h1{left:110px;top:205px;color:var(--white);font-size:41px;line-height:54px;font-family:"Fredoka",sans-serif;font-weight:500}
.card{left:745px;top:120px;width:335px;height:360px;background:var(--white);border-radius:10px;box-shadow:0 0 0 8px rgba(255,255,255,.25)}
.card h2{position:absolute;top:30px;width:100%;text-align:center;color:var(--blue);font-size:28px}
.card h2::after{content:"";display:block;width:56px;height:3px;background:var(--green);margin:4px auto 0}
.field{position:absolute;height:37px;background:#f6f6f6;border:1px solid var(--line);font-size:11px;color:#888;display:flex;align-items:center;padding-left:20px;gap:8px}
.field i{width:8px;height:9px;background:#999;border-radius:2px;display:inline-block}
.checks{position:absolute;display:flex;justify-content:space-between;font-size:13px}
.checks span{display:flex;align-items:center;gap:8px}
.checks span::before{content:"";width:11px;height:11px;border:2px solid var(--blue);border-radius:2px}
/* about */
.about-text{left:626px;top:976px;width:463px;font-size:13.5px;line-height:25.7px;color:var(--ink)}
.about-text p+p{margin-top:10px}
/* services */
.services{top:1515px;left:0;width:1200px;height:674px;background:var(--soft-blue)}
.svc{top:160px;width:306px;height:438px;background:var(--white);box-shadow:0 2px 10px rgba(0,0,0,.12);border-radius:4px}
.svc .img{position:absolute;left:7px;top:7px;width:292px;height:210px}
.svc .ico{position:absolute;left:121px;top:180px}
.svc h3{position:absolute;top:278px;width:100%;text-align:center;font-size:16px}
.svc p{position:absolute;top:306px;left:24px;width:258px;text-align:center;font-size:13.5px;line-height:24px;color:var(--muted)}
.svc .btn{left:96px;top:383px;width:114px;height:38px;font-size:11px}
/* tech */
.tech{top:2189px;left:0;width:1200px;height:428px;background:linear-gradient(90deg,#5fb603,#6dc809 60%,#7acd1c)}
/* areas */
.area-label{top:3080px;width:220px;text-align:center;font-size:17px;font-weight:700}
/* contact */
.contact{top:3198px;left:0;width:1200px;height:587px;background:var(--soft-green)}
.cfield{position:absolute;height:45px;background:var(--white);border:1px solid var(--line);font-size:13px;color:#888;display:flex;align-items:center;padding-left:20px;gap:10px}
.cfield i{width:9px;height:10px;background:#999;border-radius:2px;display:inline-block}
/* footer */
.footer{top:3785px;left:0;width:1200px;height:360px;background:linear-gradient(180deg,#1a7fd0,#1873c4);color:var(--white)}
.footer h4{position:absolute;top:60px;font-size:15px;font-weight:700}
.links{position:absolute;top:92px;left:383px;list-style:none;font-size:13px;line-height:39.5px}
.links li{display:flex;align-items:center;gap:22px}
.links li::before{content:"";width:12px;height:12px;border-radius:50%;background:var(--green)}
.info{position:absolute;left:547px;top:92px;font-size:13px}
.info .row{position:relative;padding-left:37px;margin-bottom:14px}
.info .row::before{content:"";position:absolute;left:3px;top:3px;width:11px;height:11px;background:var(--green);border-radius:2px}
.info b{display:block;font-size:13px;margin-bottom:3px}
.info small{font-size:11px;line-height:19px;display:block}
</style>
</head>
<body>

<header class="header abs">
  <div class="brand abs" style="left:111px;top:38px">
    <span class="brand-mark"></span>
    <span class="brand-name display">Quendle</span>
  </div>
  <div class="call abs">
    <svg width="38" height="38" viewBox="0 0 24 24" fill="var(--green)"><path d="M6.6 10.8a15 15 0 0 0 6.6 6.6l2.2-2.2c.3-.3.7-.4 1-.2 1.1.4 2.3.6 3.6.6.6 0 1 .4 1 1V20c0 .6-.4 1-1 1A17 17 0 0 1 3 4c0-.6.4-1 1-1h3.5c.6 0 1 .4 1 1 0 1.3.2 2.5.6 3.6.1.3 0 .7-.2 1z"/></svg>
    <div><small>CALL US:</small><b>555-014-0382</b></div>
  </div>
  <div class="social abs" style="left:928px;top:30px"><span></span><span></span><span></span><span></span></div>
  <nav class="nav abs"><span class="on">HOME</span><span>ABOUT US</span><span>SERVICES OFFERED</span><span>CONTACT</span><span>BLOG</span></nav>
</header>

<section class="hero abs" role="img" aria-label="Sunny poolside terrace with lounge chairs beside a clear blue swimming pool">
  <h1 class="abs">Keep Your Pool Sparkling<br>With Quendle!</h1>
  <span class="btn" style="left:111px;top:333px;width:141px;height:48px">Get Started</span>
  <div class="card abs">
    <h2 class="display">Lead Intake</h2>
    <div class="field" style="left:37px;top:100px;width:131px"><i></i>First Name</div>
    <div class="field" style="left:168px;top:100px;width:132px"><i></i>Last Name</div>
    <div class="field" style="left:37px;top:150px;width:131px"><i></i>Phone</div>
    <div class="field" style="left:168px;top:150px;width:132px"><i></i>Email</div>
    <div class="field" style="left:37px;top:199px;width:263px"><i></i>Address</div>
    <div class="checks" style="left:37px;top:248px;width:265px"><span>Call</span><span>Text</span><span>Email</span></div>
    <span class="btn" style="left:37px;top:280px;width:265px;height:40px;font-size:12px">Submit</span>
  </div>
</section>

<section class="about">
  <svg class="abs" style="left:100px;top:850px" width="470" height="535" viewBox="0 0 470 535" role="img" aria-label="Children jumping into a pool with inflatable floats">
    <defs><linearGradient id="aboutFill" x1="0" y1="0" x2="0" y2="1"><stop offset="0" stop-color="#5f9ecf"/><stop offset=".5" stop-color="#6fa348"/><stop offset="1" stop-color="#3fb0d8"/></linearGradient></defs>
    <polygon points="235,8 458,136 458,399 235,527 12,399 12,136" fill="url(#aboutFill)" stroke="#fff" stroke-width="7" style="filter:drop-shadow(0 2px 6px rgba(0,0,0,.25))"/>
  </svg>
  <h2 class="abs display" style="left:626px;top:893px;font-size:40px;color:var(--blue)">About Us</h2>
  <span class="abs" style="left:626px;top:948px;width:62px;height:3px;background:var(--green)"></span>
  <div class="about-text abs">
    <p>We’re Quendle Pools &amp; Patio, and we specialize in pool cleaning and repair services that will keep your pool looking its best. Our reliable and professional team is committed to helping you get the most out of your backyard oasis, ensuring it’s always ready for all types of fun when you want it. Our weekly pool cleaning service is affordable and ensures that your pool is properly taken care of throughout the swimming season.</p>
    <p>When you choose us as your go-to for all things pools, relaxing days spent on a clean lounge chair are worry-free because we take care of all the hard work!</p>
  </div>
  <span class="btn" style="left:626px;top:1272px;width:142px;height:48px">Lead Intake</span>
</section>

<section class="services abs">
  <h2 class="section-title display" style="top:60px">Our Services</h2>
  <div class="svc abs" style="left:111px">
    <div class="img" role="img" aria-label="Pool skimmer net holding autumn leaves over blue water" style="background:linear-gradient(135deg,#2aa7e0,#1e5fc8 50%,#d98a2a 70%,#37b5e6)"></div>
    <svg class="ico" width="64" height="72" viewBox="0 0 64 72"><polygon points="32,2 62,19 62,53 32,70 2,53 2,19" fill="var(--blue)"/><path d="M18 44c4-3 6-3 10 0s6 3 10 0 6-3 10 0M22 38V26M32 38V26M22 30h10" stroke="#fff" stroke-width="2.5" fill="none"/></svg>
    <h3>POOL CLEANING</h3>
    <p>Our weekly service includes chemical balancing, debris removal, wall and step scrubbing</p>
    <span class="btn">Learn More</span>
  </div>
  <div class="svc abs" style="left:447px">
    <div class="img" role="img" aria-label="Pool vacuum hose running into clear water" style="background:linear-gradient(160deg,#c9b79a,#8aa3a8 45%,#3a9ac0 75%,#6cc0dc)"></div>
    <svg class="ico" width="64" height="72" viewBox="0 0 64 72"><polygon points="32,2 62,19 62,53 32,70 2,53 2,19" fill="var(--blue)"/><circle cx="32" cy="32" r="9" stroke="#fff" stroke-width="2.5" fill="none"/><path d="M18 50h28" stroke="#fff" stroke-width="2.5"/></svg>
    <h3>POOL MAINTENANCE</h3>
    <p>We perform regular checks on all your pool equipment to make sure it runs efficiently and safely.</p>
    <span class="btn">Learn More</span>
  </div>
  <div class="svc abs" style="left:783px">
    <div class="img" role="img" aria-label="Technician working at the edge of a pool beside a wooden deck" style="background:linear-gradient(110deg,#6b5440,#8c7862 25%,#27a6dc 45%,#3cc0e8)"></div>
    <svg class="ico" width="64" height="72" viewBox="0 0 64 72"><polygon points="32,2 62,19 62,53 32,70 2,53 2,19" fill="var(--blue)"/><path d="M20 48l24-24M20 24l24 24" stroke="#fff" stroke-width="3"/></svg>
    <h3>POOL REPAIR</h3>
    <p>From plumbing to equipment malfunctions, our qualified technicians can diagnose</p>
    <span class="btn">Learn More</span>
  </div>
</section>

<section class="tech abs">
  <h2 class="abs display" style="left:174px;top:70px;font-size:38px;color:var(--white)">Meet Your Technician</h2>
  <h3 class="abs" style="left:174px;top:148px;font-size:22px;color:var(--white)">DALE MERRITT</h3>
  <p class="abs" style="left:174px;top:192px;width:510px;font-size:13px;line-height:26px;font-weight:700;color:var(--white)">I understand that keeping your pool clean and well-maintained is a priority for you, which is why I’m committed to providing top-notch pool cleaning and repair services.</p>
  <span class="btn btn-blue" style="left:174px;top:303px;width:150px;height:48px">Get Started</span>
  <div class="abs" role="img" aria-label="Portrait of the pool technician" style="left:735px;top:64px;width:300px;height:300px;border-radius:50%;border:6px solid #fff;background:linear-gradient(160deg,#d8d8d8,#9a9a9a);box-shadow:0 0 0 2px rgba(0,0,0,.15)"></div>
</section>

<section class="areas">
  <h2 class="section-title display" style="top:2700px">Service Areas</h2>
  <svg class="abs" style="left:100px;top:2790px" width="1000" height="270" viewBox="0 0 1000 270">
    <defs>
      <linearGradient id="a1" x1="0" y1="0" x2="0" y2="1"><stop offset="0" stop-color="#9cc3e0"/><stop offset="1" stop-color="#4f7a4a"/></linearGradient>
      <linearGradient id="a2" x1="0" y1="0" x2="0" y2="1"><stop offset="0" stop-color="#bcd3e6"/><stop offset="1" stop-color="#9a7a5a"/></linearGradient>
      <linearGradient id="a3" x1="0" y1="0" x2="0" y2="1"><stop offset="0" stop-color="#e4877a"/><stop offset=".6" stop-color="#6d7a9a"/><stop offset="1" stop-color="#3f5a4a"/></linearGradient>
      <linearGradient id="a4" x1="0" y1="0" x2="0" y2="1"><stop offset="0" stop-color="#2f6fd4"/><stop offset="1" stop-color="#4a7a34"/></linearGradient>
    </defs>
    <g stroke="#fff" stroke-width="6" style="filter:drop-shadow(0 2px 5px rgba(0,0,0,.25))">
      <polygon role="img" aria-label="Texas city skyline with highways" points="122,5 230,68 230,198 122,261 14,198 14,68" fill="url(#a1)"/>
      <polygon role="img" aria-label="Corinth landmark columns" points="374,5 482,68 482,198 374,261 266,198 266,68" fill="url(#a2)"/>
      <polygon role="img" aria-label="Flower Mound skyline at sunset" points="626,5 734,68 734,198 626,261 518,198 518,68" fill="url(#a3)"/>
      <polygon role="img" aria-label="Lewisville river walk with trees" points="878,5 986,68 986,198 878,261 770,198 770,68" fill="url(#a4)"/>
    </g>
  </svg>
  <div class="area-label abs" style="left:112px">TEXAS</div>
  <div class="area-label abs" style="left:364px">CORINTH</div>
  <div class="area-label abs" style="left:616px">FLOWER MOUND</div>
  <div class="area-label abs" style="left:868px">LEWISVILLE</div>
</section>

<section class="contact abs">
  <h2 class="section-title display" style="top:45px">Contact Us</h2>
  <p class="abs" style="left:150px;top:128px;width:900px;text-align:center;font-size:13.5px;line-height:26px">Contact us today at Quendle Pools &amp; Patio, and let’s discuss how our professionals can help bridge the gap between what your pool could be and what it actually is! Get ready to have a worry-free experience with quality service delivered right on time so you can start enjoying those waves anytime soon!</p>
  <p class="abs" style="left:0;top:218px;width:1200px;text-align:center;font-size:17px">Give us a call today at <b style="color:var(--green);text-decoration:underline">555-014-0382</b></p>
  <div class="cfield" style="left:278px;top:274px;width:322px"><i></i>First Name</div>
  <div class="cfield" style="left:600px;top:274px;width:322px"><i></i>Last Name</div>
  <div class="cfield" style="left:278px;top:332px;width:322px"><i></i>Phone</div>
  <div class="cfield" style="left:600px;top:332px;width:322px"><i></i>Email</div>
  <div class="cfield" style="left:278px;top:389px;width:644px"><i></i>Address</div>
  <div class="checks" style="left:433px;top:447px;width:334px;font-size:14px"><span>Call</span><span>Text</span><span>Email</span></div>
  <span class="btn" style="left:529px;top:488px;width:142px;height:47px">Submit</span>
</section>

<footer class="footer abs">
  <div class="brand abs" style="left:111px;top:125px">
    <span class="brand-mark" style="width:42px;height:42px"></span>
    <span class="brand-name display" style="color:var(--white);font-size:46px">Quendle</span>
  </div>
  <h4 style="left:383px">QUICK LINKS</h4>
  <ul class="links"><li>Home</li><li>About Us</li><li>Services Offered</li><li>Contact</li><li>Blog</li></ul>
  <h4 style="left:547px">CONTACT INFO</h4>
  <div class="info">
    <div class="row"><b>ADDRESS:</b><small>Mailing Address: 1180 Harbor Lane,<br>Suite 110, Maplewood, TX 75000</small></div>
    <div class="row"><b>PHONE:</b><small>555-014-0382</small></div>
    <div class="row"><b>EMAIL:</b><small>info@quendle-example.com</small></div>
  </div>
  <h4 style="left:790px">NEWSLETTER SIGNUP</h4>
  <div class="abs" style="left:790px;top:98px;width:299px;height:45px;background:var(--white);display:flex;align-items:center;justify-content:space-between;padding:0 16px 0 18px;font-size:13px;color:#888">Email
    <svg width="16" height="16" viewBox="0 0 24 24"><path d="M2 12L22 3 16 21 11 14z" fill="none" stroke="var(--green)" stroke-width="2"/></svg>
  </div>
  <div class="social abs" style="left:790px;top:173px"><span></span><span></span><span></span><span></span></div>
  <span class="abs" style="left:111px;top:316px;width:978px;height:1px;background:rgba(255,255,255,.35)"></span>
  <p class="abs" style="left:0;top:332px;width:1200px;text-align:center;font-size:11px">© 2023 QUENDLE &nbsp;&nbsp;|&nbsp;&nbsp; All Rights Reserved</p>
</footer>

</body>
</html>
```